Business Card Design for Training Business

Clear Path Coaching is a new business that delivers training and other services with a focus on topics related to mental health and wellbeing, for example, Wellmind Response Course, Resilience etc. We have a strong focus on evidence-based psychology and neuroscience. I have a logo which I will upload with the brief, so please consider colours that work well with the logo.
Target Market(s)
Adults, workplaces (particularly government and not-for-profits)
Industry/Entity Type
Business
Contact Information for Business Card
Head Strong TrainingSamantha SellwoodDirector0438 770 850sam@headstrongtraining.com.auwww.headstrongtraining.com.au

```html
<!DOCTYPE html>
<html lang="en">
<head>
<meta charset="utf-8">
<title>Clear Path Coaching – Business Card</title>
<link href="https://fonts.googleapis.com/css2?family=Josefin+Sans:wght@300&family=Arimo:wght@400&display=swap" rel="stylesheet">
<style>
  :root {
    --backdrop: #e7e2dc;
    --card-light: #f1f2f1;
    --card-mist: #dfe6e6;
    --teal: #2f9a8e;
    --teal-deep: #23807a;
    --swoosh: #5a4d4b;
    --brand-ink: #3f3a3a;
    --rose: #ecd0cb;
    --rose-deep: #d9aaa6;
  }
  * { margin: 0; padding: 0; box-sizing: border-box; }
  html, body {
    width: 1200px;
    height: 970px;
    overflow: hidden;
    background: var(--backdrop);
  }
  .card {
    position: absolute;
    left: 65px;
    top: 165px;
    width: 1070px;
    height: 640px;
    border-radius: 6px;
    overflow: hidden;
    background: linear-gradient(160deg, var(--card-light) 0%, var(--card-mist) 100%);
    box-shadow: 0 10px 30px rgba(60, 50, 45, 0.18);
  }
  .card-shapes {
    position: absolute;
    inset: 0;
    width: 1070px;
    height: 640px;
  }
  .brand {
    position: absolute;
    left: 0;
    width: 1070px;
    text-align: center;
    font-family: "Josefin Sans", sans-serif;
    font-weight: 300;
    color: var(--brand-ink);
  }
  .brand-main {
    top: 308px;
    font-size: 58px;
    letter-spacing: 5px;
  }
  .brand-sub {
    top: 385px;
    font-size: 28px;
    letter-spacing: 9px;
  }
  .person {
    position: absolute;
    left: 40px;
    top: 505px;
    width: 460px;
    text-align: right;
    font-family: "Arimo", sans-serif;
    color: var(--rose);
  }
  .person-name {
    font-size: 46px;
    line-height: 54px;
  }
  .person-role {
    font-size: 33px;
    line-height: 38px;
  }
  .divider {
    position: absolute;
    left: 525px;
    top: 495px;
    width: 2px;
    height: 118px;
    background: var(--rose-deep);
  }
  .contacts {
    position: absolute;
    left: 552px;
    top: 500px;
    list-style: none;
    font-family: "Arimo", sans-serif;
    font-size: 26px;
    color: var(--rose);
  }
  .contact-item {
    display: flex;
    align-items: center;
    height: 38px;
  }
  .contact-icon {
    width: 22px;
    height: 22px;
    margin-right: 14px;
    flex: none;
  }
</style>
</head>
<body>
  <div class="card">
    <svg class="card-shapes" viewBox="0 0 1070 640" aria-hidden="true">
      <defs>
        <linearGradient id="tealFill" x1="0" y1="0" x2="1" y2="1">
          <stop offset="0" stop-color="var(--teal)"/>
          <stop offset="1" stop-color="var(--teal-deep)"/>
        </linearGradient>
      </defs>
      <path class="teal-band" fill="url(#tealFill)"
            d="M0,245 C120,420 330,490 560,485 C800,480 980,300 1070,120 L1070,640 L0,640 Z"/>
      <path class="swoosh" fill="var(--swoosh)"
            d="M0,130 C80,360 300,470 560,460 C760,452 880,360 935,280 C860,370 740,440 560,445 C330,450 120,360 0,175 Z"/>
      <circle class="brand-mark" cx="535" cy="155" r="98" fill="none" stroke="var(--teal)" stroke-width="3"/>
    </svg>

    <div class="brand brand-main">CLEAR PATH</div>
    <div class="brand brand-sub">COACHING</div>

    <div class="person">
      <div class="person-name">Rebecca Tanfield</div>
      <div class="person-role">Director</div>
    </div>

    <div class="divider"></div>

    <ul class="contacts">
      <li class="contact-item">
        <svg class="contact-icon" viewBox="0 0 22 22" aria-hidden="true">
          <rect width="22" height="22" rx="3" fill="var(--rose-deep)"/>
          <path d="M6 5 L9 5 L10 8 L8.5 9.5 C9.5 11.5 10.5 12.5 12.5 13.5 L14 12 L17 13 L17 16 C11 17 5 11 6 5 Z" fill="var(--teal-deep)"/>
        </svg>
        <span>0491 362 517</span>
      </li>
      <li class="contact-item">
        <svg class="contact-icon" viewBox="0 0 22 22" aria-hidden="true">
          <rect width="22" height="22" rx="3" fill="var(--rose-deep)"/>
          <rect x="4" y="6" width="14" height="10" fill="none" stroke="var(--teal-deep)" stroke-width="1.6"/>
          <path d="M4 6 L11 12 L18 6" fill="none" stroke="var(--teal-deep)" stroke-width="1.6"/>
        </svg>
        <span>bec@clearpathcoaching.example.au</span>
      </li>
      <li class="contact-item">
        <svg class="contact-icon" viewBox="0 0 22 22" aria-hidden="true">
          <rect width="22" height="22" rx="3" fill="var(--rose-deep)"/>
          <circle cx="11" cy="11" r="6.5" fill="none" stroke="var(--teal-deep)" stroke-width="1.6"/>
          <path d="M4.5 11 H17.5 M11 4.5 C8 8 8 14 11 17.5 M11 4.5 C14 8 14 14 11 17.5" fill="none" stroke="var(--teal-deep)" stroke-width="1.3"/>
        </svg>
        <span>www.clearpathcoaching.example.au</span>
      </li>
    </ul>
  </div>
</body>
</html>
```